Brovenna a national investment company

We need a logo/letterhead design to describe our business. We use our business across the country to buy and sale property, buy property mineral rights, make investments in small businesses. Our business goal is to promotes integrity, security and growth in small investments. We want our product to reflect our goals.
Updates
I "think" I want a modern, sleek, not too busy design. I "think" I want a dark green and black/grey colors. However, y'all know best and I am looking forward to seeing your creativity in our design. Thanks for accepting our project. -Delphine
We are pleased with some of the designs submitted. We would like for the designs to reflect our company name as it appears on our license, Brovenna. We appreciate the designers who took into consideration our colors we specified. Thanks for all the hard work. We will make a decision tomorrow. You still have time to submit more ideas.
Industry/Entity Type
Investment
Logo Text
Brovenna LLC
Look and feel
Each slider illustrates characteristics of the customer's brand and the style your logo design should communicate.

```html
<!DOCTYPE html>
<html lang="en">
<head>
<meta charset="utf-8">
<title>Brovenna Letterhead</title>
<link rel="stylesheet" href="https://fonts.googleapis.com/css2?family=Roboto:wght@400;700&display=swap">
<style>
  :root {
    --backdrop: #e9e9ea;
    --paper: #ffffff;
    --ink: #2b2b2b;
    --accent: #e07a10;
    --rule: #8a8a8a;
    --band: #1f1f1f;
    --band-text: #f2f2f2;
  }
  * { margin: 0; padding: 0; box-sizing: border-box; }
  html, body {
    width: 1200px;
    height: 943px;
    overflow: hidden;
    background: var(--backdrop);
    font-family: "Roboto", Arial, sans-serif;
  }
  .letterhead {
    position: absolute;
    left: 281px;
    top: 16px;
    width: 638px;
    height: 911px;
    background: var(--paper);
    box-shadow: 0 2px 10px rgba(0,0,0,0.12);
  }
  .letterhead__header {
    position: absolute;
    left: 0;
    right: 0;
    top: 0;
    height: 140px;
    border-bottom: 1px solid var(--rule);
  }
  .brand {
    position: absolute;
    left: 48px;
    top: 58px;
  }
  .brand__name {
    display: flex;
    align-items: center;
    gap: 8px;
    font-weight: 700;
    font-size: 30px;
    letter-spacing: 1px;
    color: var(--ink);
    line-height: 1;
  }
  .brand__mark {
    width: 12px;
    height: 12px;
    background: var(--accent);
  }
  .brand__tagline {
    margin-top: 5px;
    margin-left: 20px;
    font-size: 10px;
    color: var(--accent);
    letter-spacing: 0.3px;
  }
  .letterhead__footer {
    position: absolute;
    left: 0;
    right: 0;
    bottom: 36px;
    height: 22px;
    background: var(--band);
    display: flex;
    justify-content: flex-end;
    align-items: center;
    gap: 16px;
    padding: 0 18px;
  }
  .contact-item {
    display: flex;
    align-items: center;
    gap: 5px;
    font-size: 10.5px;
    color: var(--band-text);
    white-space: nowrap;
  }
  .contact-item svg { width: 11px; height: 11px; flex: none; }
</style>
</head>
<body>
  <main class="letterhead">
    <header class="letterhead__header">
      <div class="brand">
        <div class="brand__name"><span class="brand__mark"></span>BROVENNA</div>
        <div class="brand__tagline">A National Investment Company</div>
      </div>
    </header>

    <footer class="letterhead__footer">
      <span class="contact-item">
        <svg viewBox="0 0 12 12" aria-hidden="true"><circle cx="6" cy="6" r="6" fill="var(--accent)"/><path d="M6 2.6a2.2 2.2 0 0 0-2.2 2.2C3.8 6.5 6 9.4 6 9.4s2.2-2.9 2.2-4.6A2.2 2.2 0 0 0 6 2.6zm0 3a.8.8 0 1 1 0-1.6.8.8 0 0 1 0 1.6z" fill="var(--band)"/></svg>
        Address Here Address Here Address
      </span>
      <span class="contact-item">
        <svg viewBox="0 0 12 12" aria-hidden="true"><circle cx="6" cy="6" r="6" fill="var(--accent)"/><path d="M4 3l1.2 1.4-.6.8c.4.9 1 1.5 1.9 1.9l.8-.6L8.7 7.7 8 9C5.5 8.8 3.2 6.5 3 4z" fill="var(--band)"/></svg>
        02 5550 1847
      </span>
      <span class="contact-item">
        <svg viewBox="0 0 12 12" aria-hidden="true"><circle cx="6" cy="6" r="6" fill="var(--accent)"/><rect x="3" y="4" width="6" height="4.2" fill="var(--band)"/><path d="M3 4l3 2.4L9 4" stroke="var(--accent)" stroke-width=".7" fill="none"/></svg>
        info@brovenna.com
      </span>
      <span class="contact-item">
        <svg viewBox="0 0 12 12" aria-hidden="true"><circle cx="6" cy="6" r="6" fill="var(--accent)"/><circle cx="6" cy="6" r="3" fill="none" stroke="var(--band)" stroke-width=".8"/><path d="M3 6h6M6 3c-1.3 1.6-1.3 4.4 0 6M6 3c1.3 1.6 1.3 4.4 0 6" stroke="var(--band)" stroke-width=".7" fill="none"/></svg>
        www.brovenna.com
      </span>
    </footer>
  </main>
</body>
</html>
```